Billboard design 8x3M RAVU (Spanish company)

We´re located in the south of Spain. We run a local telecom company.
We sell Fiber optic, and mobile phone lines mainly.
The billboard will have to be in Spanish, I would like the price to be something you spot on first sight when passing by in the car.
Our company color is blue, like in our logo which I will add. I will also add a example from what we currently have.
The new offer should be:
1000 megas + 100Gigas movil con llamadas ilimitadas. (meaning 1000Mb fiber optic speed and 100Gb data and unlimited calls for 1 mobile line)
Our details are: phone line 958 47 6620
Website: ra-vu.es

```html
<!DOCTYPE html>
<html lang="es">
<head>
<meta charset="utf-8">
<title>RAVU – Valla 8x3 – Oferta Fibra + Móvil</title>
<link href="https://fonts.googleapis.com/css2?family=Exo+2:wght@600;700&family=Montserrat:wght@700;800&display=swap" rel="stylesheet">
<style>
  :root {
    --brand-navy: #0a5a8c;
    --brand-sky: #00c3f5;
    --paper: #ffffff;
    --backdrop: #e9eef2;
  }
  html, body {
    margin: 0;
    padding: 0;
    width: 1200px;
    height: 874px;
    overflow: hidden;
    background: var(--backdrop);
  }
  .billboard {
    position: absolute;
    left: 20px;
    top: 232px;
    width: 1160px;
    height: 410px;
    background: var(--paper);
    overflow: hidden;
  }
  .billboard__art { display: block; }
  .price, .price__label, .brand__name, .brand__services {
    font-family: "Montserrat", sans-serif;
  }
  .price { font-weight: 800; font-size: 146px; fill: var(--paper); }
  .price__label { font-weight: 800; font-size: 42px; fill: var(--paper); }
  .web__url, .offer, .offer__detail, .phone {
    font-family: "Exo 2", sans-serif;
  }
  .web__url { font-weight: 700; font-size: 58px; fill: var(--brand-sky); }
  .offer { font-weight: 600; font-size: 66px; fill: var(--paper); }
  .offer__detail { font-weight: 700; font-size: 50px; fill: var(--brand-navy); }
  .phone { font-weight: 700; font-size: 84px; fill: var(--paper); }
  .brand__name { font-weight: 800; font-size: 56px; fill: var(--brand-sky); }
  .brand__services { font-weight: 700; font-size: 15px; fill: var(--brand-navy); }
</style>
</head>
<body>
  <section class="billboard" aria-label="Valla publicitaria RAVU">
    <svg class="billboard__art" width="1160" height="410" viewBox="0 0 1160 410">
      <path class="band-sky" d="M300 305 H840 A75 75 0 0 1 915 380 V410 H290 Z" fill="var(--brand-sky)"/>
      <path class="arc-dashed" d="M320 0 C440 95 440 290 305 410" fill="none" stroke="var(--brand-sky)" stroke-width="5" stroke-dasharray="18 12"/>
      <path class="panel-navy" d="M0 0 H295 C415 95 415 290 280 410 H0 Z" fill="var(--brand-navy)"/>

      <text class="price" x="44" y="227" textLength="292" lengthAdjust="spacingAndGlyphs">35€</text>
      <text class="price__label" x="46" y="285" textLength="227" lengthAdjust="spacingAndGlyphs">POR SÓLO</text>

      <g class="web">
        <path d="M634 52 L668 40 L654 74 L651 57 Z" fill="var(--brand-navy)"/>
        <path d="M669 30 V37 M676 34 L671 39 M680 45 H673" stroke="var(--brand-navy)" stroke-width="3" stroke-linecap="round"/>
        <text class="web__url" x="688" y="72" textLength="230" lengthAdjust="spacingAndGlyphs">ra-vu.es</text>
      </g>

      <rect class="offer__box" x="428" y="99" width="714" height="86" rx="12" fill="var(--brand-navy)"/>
      <text class="offer" x="443" y="167" textLength="684" lengthAdjust="spacingAndGlyphs">1000 MEGAS + 100GIGAS</text>
      <text class="offer__detail" x="441" y="232" textLength="687" lengthAdjust="spacingAndGlyphs">MOVIL CON LLAMADAS ILIMITADAS</text>

      <text class="phone" x="403" y="383" textLength="438" lengthAdjust="spacingAndGlyphs">958 47 6620</text>

      <text class="brand__name" x="932" y="352" textLength="195" lengthAdjust="spacingAndGlyphs">RAVU</text>
      <text class="brand__services" x="934" y="375" textLength="192" lengthAdjust="spacingAndGlyphs">Wifi | Fibra | Movil | Tv</text>
    </svg>
  </section>
</body>
</html>
```